Business Card Design for company

We want new business cards. We'd like something different-- yet still highly professional. Our tagline is Guiding Strategy, Building Results. Stock photos are ok, as long as they are relevant and look upscale.

Target Market(s)

Architecture/Business Management Consulting/Engineering Consulting

Contact Information for Business Card

dark gray background with pops of blue might be good, but you tell me. You're the designers. Rounded corners might be nice, but again, you tell me.

Font styles to use
Serif
Sans Serif

Colors
3276b5
5c5c5c
9d9d9d
fbfbfb

Requirements
Nice to have
• Something different, but still very professional.

```html
<!DOCTYPE html>
<html lang="en">
<head>
<meta charset="utf-8">
<title>Halden Group – Business Card</title>
<link href="https://fonts.googleapis.com/css2?family=Exo+2:wght@400;500;600;700&display=swap" rel="stylesheet">
<style>
  :root {
    --blue: #3276b5;
    --blue-deep: #2a64a0;
    --gray: #5c5c5c;
    --gray-light: #9d9d9d;
    --paper: #fbfbfb;
    --ink: #1e1e1e;
    --charcoal: #2a2a2a;
    --charcoal-dark: #1c1c1c;
    --stage: #e9e9e9;
  }
  * { margin: 0; padding: 0; box-sizing: border-box; }
  html, body { width: 1200px; height: 900px; overflow: hidden; }
  body {
    background: var(--stage);
    font-family: "Exo 2", sans-serif;
    position: relative;
  }
  .card {
    position: absolute;
    left: 320px;
    width: 560px;
    height: 320px;
    border-radius: 18px;
    overflow: hidden;
    box-shadow: 0 10px 28px rgba(0,0,0,0.18);
  }

  /* Back side */
  .card-back {
    top: 90px;
    background: radial-gradient(ellipse at 50% 40%, var(--charcoal) 0%, var(--charcoal-dark) 100%);
    display: flex;
    flex-direction: column;
    align-items: center;
    justify-content: center;
    gap: 18px;
  }
  .brand {
    display: flex;
    align-items: center;
    gap: 10px;
    color: var(--blue);
    font-weight: 700;
    letter-spacing: 1px;
    text-transform: uppercase;
    white-space: nowrap;
  }
  .brand-mark { width: 14px; height: 14px; background: var(--blue); flex: none; }
  .card-back .brand { font-size: 44px; }
  .card-back .brand-mark { width: 18px; height: 18px; }
  .tagline {
    color: var(--paper);
    font-size: 18px;
    font-weight: 400;
    letter-spacing: 0.5px;
  }

  /* Front side */
  .card-front {
    top: 490px;
    background: var(--paper);
  }
  .card-front .brand {
    position: absolute;
    left: 36px;
    top: 42px;
    font-size: 27px;
  }
  .card-front .brand-mark { width: 12px; height: 12px; }
  .person {
    position: absolute;
    right: 36px;
    top: 64px;
    text-align: right;
  }
  .person-name {
    font-size: 22px;
    font-weight: 600;
    color: var(--ink);
    letter-spacing: 1px;
    white-space: nowrap;
  }
  .person-title {
    font-size: 15px;
    font-weight: 600;
    color: var(--blue);
    margin-top: 2px;
  }
  .divider {
    position: absolute;
    left: 36px;
    right: 36px;
    top: 140px;
    height: 3px;
    display: flex;
  }
  .divider-dark { flex: 0 0 58%; background: var(--ink); }
  .divider-blue { flex: 1; background: var(--blue); height: 2px; }
  .contacts {
    position: absolute;
    left: 36px;
    top: 168px;
    list-style: none;
    display: flex;
    flex-direction: column;
    gap: 7px;
  }
  .contact {
    display: flex;
    align-items: center;
    gap: 14px;
    font-size: 16px;
    color: var(--ink);
  }
  .contact svg { width: 18px; height: 18px; fill: var(--blue-deep); flex: none; }
  .address {
    position: absolute;
    right: 36px;
    top: 196px;
    display: flex;
    align-items: flex-start;
    gap: 12px;
    font-size: 16px;
    color: var(--ink);
    text-align: right;
    font-style: normal;
    line-height: 1.35;
  }
  .address svg { width: 16px; height: 20px; fill: var(--blue-deep); margin-top: 2px; flex: none; }
  .edge-band {
    position: absolute;
    left: 0; right: 0; bottom: 0;
    height: 16px;
    background: var(--blue);
  }
</style>
</head>
<body>

<section class="card card-back" aria-label="Card back">
  <div class="brand"><span class="brand-mark"></span>Halden Group</div>
  <p class="tagline">Guiding Strategy, Building Results</p>
</section>

<section class="card card-front" aria-label="Card front">
  <div class="brand"><span class="brand-mark"></span>Halden Group</div>

  <div class="person">
    <p class="person-name">DANIEL BROOKS</p>
    <p class="person-title">CEO | Founder</p>
  </div>

  <div class="divider"><span class="divider-dark"></span><span class="divider-blue"></span></div>

  <ul class="contacts">
    <li class="contact">
      <svg viewBox="0 0 24 24" aria-hidden="true"><path d="M3 9c0-3 4-5 9-5s9 2 9 5v2h-5V9c-1-.6-2.4-1-4-1s-3 .4-4 1v2H3z"/><rect x="5" y="13" width="14" height="8" rx="2"/></svg>
      555-014-2087
    </li>
    <li class="contact">
      <svg viewBox="0 0 24 24" aria-hidden="true"><path d="M6.6 10.8a15 15 0 0 0 6.6 6.6l2.2-2.2a1 1 0 0 1 1-.25 11.4 11.4 0 0 0 3.6.57 1 1 0 0 1 1 1V20a1 1 0 0 1-1 1A17 17 0 0 1 3 4a1 1 0 0 1 1-1h3.5a1 1 0 0 1 1 1c0 1.25.2 2.45.57 3.57a1 1 0 0 1-.25 1z"/></svg>
      555-014-2086
    </li>
    <li class="contact">
      <svg viewBox="0 0 24 24" aria-hidden="true"><path d="M2 5h20v2l-10 6L2 7z"/><path d="M2 9l10 6 10-6v10H2z"/></svg>
      brooks@haldengroup.com
    </li>
    <li class="contact">
      <svg viewBox="0 0 24 24" aria-hidden="true"><path d="M12 2a10 10 0 1 0 0 20 10 10 0 0 0 0-20zm6.9 9h-3a15 15 0 0 0-1.3-5.9A8 8 0 0 1 18.9 11zM12 4.1c.9 1.2 1.8 3.6 1.9 6.9h-3.8c.1-3.300 1-5.700 1.900-6.900zM9.4 5.1A15 15 0 0 0 8.1 11h-3a8 8 0 0 1 4.3-5.9zM5.1 13h3a15 15 0 0 0 1.3 5.9A8 8 0 0 1 5.1 13zm6.9 6.9c-.9-1.2-1.8-3.6-1.9-6.9h3.8c-.1 3.3-1 5.7-1.9 6.9zm2.6-1a15 15 0 0 0 1.3-5.9h3a8 8 0 0 1-4.3 5.9z"/></svg>
      www.haldengroup.com
    </li>
  </ul>

  <address class="address">
    <span>480 Alder Crest Road,<br>Suite 210 Fairview, NY 10990</span>
    <svg viewBox="0 0 16 20" aria-hidden="true"><path d="M8 0a7 7 0 0 0-7 7c0 5 7 13 7 13s7-8 7-13a7 7 0 0 0-7-7zm0 9.5A2.5 2.5 0 1 1 8 4.5a2.5 2.5 0 0 1 0 5z"/></svg>
  </address>

  <div class="edge-band"></div>
</section>

</body>
</html>
```